Vantiqo custom business card design

Need a authentic, innovative business card design for a new mobile app business. I am uploading a few screen images from our app for you to view. I would like app design theme to match business card design. I can also send logo images.

```html
<!DOCTYPE html>
<html lang="en">
<head>
<meta charset="UTF-8">
<title>Vantiqo Business Card</title>
<link href="https://fonts.googleapis.com/css2?family=Montserrat:wght@700;800&family=Open+Sans:wght@400&display=swap" rel="stylesheet">
<style>
  :root {
    --backdrop: #5c5c5c;
    --card-light: #f3f3f3;
    --brand-purple: #5f008e;
    --ink-dark: #1e1e1e;
    --ink-body: #2a2a2a;
    --white: #ffffff;
  }
  * { margin: 0; padding: 0; box-sizing: border-box; }
  html, body {
    width: 1200px;
    height: 900px;
    overflow: hidden;
    background: var(--backdrop);
  }
  .canvas {
    position: relative;
    width: 1200px;
    height: 900px;
  }
  .card {
    position: absolute;
    top: 200px;
    width: 310px;
    height: 502px;
  }
  .card-front {
    left: 253px;
    background: var(--card-light);
    border-radius: 52px 0 52px 0;
  }
  .card-back {
    left: 627px;
    background: var(--brand-purple);
    border-radius: 0 52px 0 52px;
  }
  .brand-block {
    position: absolute;
    top: 58px;
    left: 0;
    width: 100%;
    text-align: center;
  }
  .brand-dot {
    display: block;
    width: 110px;
    height: 110px;
    margin: 0 auto 22px;
    border-radius: 50%;
    background: var(--brand-purple);
  }
  .brand-name {
    font-family: "Montserrat", sans-serif;
    font-weight: 800;
    font-size: 37px;
    line-height: 1;
    color: var(--ink-dark);
  }
  .contact-block {
    position: absolute;
    left: 33px;
    top: 301px;
    font-family: "Open Sans", sans-serif;
    color: var(--ink-body);
  }
  .person-name {
    font-family: "Montserrat", sans-serif;
    font-weight: 700;
    font-size: 21px;
    line-height: 24px;
    color: var(--brand-purple);
    letter-spacing: 0.2px;
  }
  .person-title {
    font-size: 15px;
    line-height: 20px;
    margin-bottom: 5px;
  }
  .contact-list { list-style: none; }
  .contact-item {
    display: flex;
    align-items: center;
    font-size: 15px;
    line-height: 18px;
  }
  .contact-icon {
    width: 12px;
    height: 12px;
    margin-right: 4px;
    fill: var(--brand-purple);
    flex: none;
  }
  .address {
    font-style: normal;
    font-size: 15px;
    line-height: 18px;
    margin-top: 8px;
  }
  .back-brand {
    position: absolute;
    top: 50%;
    left: 0;
    width: 100%;
    transform: translateY(-50%);
    text-align: center;
  }
  .back-dot {
    display: block;
    width: 64px;
    height: 64px;
    margin: 0 auto 16px;
    border-radius: 50%;
    background: var(--white);
  }
  .back-name {
    font-family: "Montserrat", sans-serif;
    font-weight: 800;
    font-size: 34px;
    line-height: 1;
    color: var(--white);
  }
</style>
</head>
<body>
<main class="canvas">
  <section class="card card-front">
    <div class="brand-block">
      <span class="brand-dot"></span>
      <div class="brand-name">Vantiqo</div>
    </div>
    <div class="contact-block">
      <h1 class="person-name">DANIEL HARPER</h1>
      <p class="person-title">Managing Director</p>
      <ul class="contact-list">
        <li class="contact-item">
          <svg class="contact-icon" viewBox="0 0 12 12"><path d="M1 4c0-2 2-3 5-3s5 1 5 3l-2 1-1-1V3H4v1L3 5 1 4zM2 6h8l1 5H1l1-5zm4 1a1.5 1.5 0 1 0 0 3 1.5 1.5 0 0 0 0-3z"/></svg>
          044-555 210 348
        </li>
        <li class="contact-item">
          <svg class="contact-icon" viewBox="0 0 12 12"><path d="M3.5 0h5a1 1 0 0 1 1 1v10a1 1 0 0 1-1 1h-5a1 1 0 0 1-1-1V1a1 1 0 0 1 1-1zm.5 1.5v7.5h4V1.5H4zM6 10a.6.6 0 1 0 0 1.2A.6.6 0 0 0 6 10z"/></svg>
          044-555 210 349
        </li>
        <li class="contact-item">
          <svg class="contact-icon" viewBox="0 0 12 12"><path d="M0 2.5h12v7H0v-7zm1 .8L6 6.8l5-3.5V3H1v.3z"/></svg>
          hello@vantiqo.app
        </li>
        <li class="contact-item">
          <svg class="contact-icon" viewBox="0 0 12 12"><circle cx="6" cy="6" r="5.5"/><path d="M4 3.5l2 1-1 2 2 1-1 2" stroke="#f3f3f3" stroke-width="1" fill="none"/></svg>
          www.vantiqo.app
        </li>
      </ul>
      <address class="address">48 Harbour Lane<br>Brightwater, 560218.</address>
    </div>
  </section>

  <section class="card card-back">
    <div class="back-brand">
      <span class="back-dot"></span>
      <div class="back-name">Vantiqo</div>
    </div>
  </section>
</main>
</body>
</html>
```